RWT Fittings Ltd Business Cards

We need a business card with our business logo. We provide window and door installations on high-rises in west coast British Colombia, Canada.

I would like my business information and details on one side of the card, and the other side the company name with logo

Target Market(s)

General Contractors

Industry/Entity Type

Construction

Contact Information for Business Card

one side i want my company name and logo in the dark theme logo that i provided

Requirements
Must have
• Marco Peltieri, 16045518293, RWTFittings@mailbox-demo.com, 1407-5194 Linden Row Burnaby BC, V5H 2K9, Owner & Manager

```html
<!DOCTYPE html>
<html lang="en">
<head>
<meta charset="utf-8">
<title>RWT Fittings Ltd Business Cards</title>
<link href="https://fonts.googleapis.com/css2?family=Poppins:wght@400;600;700&display=swap" rel="stylesheet">
<style>
  :root {
    --stage: #1c1b1b;
    --card-white: #ffffff;
    --brand-blue: #25a7e0;
    --brand-cyan: #2ec6f2;
    --dark-card-a: #2e2b29;
    --dark-card-b: #3f3a37;
    --text-white: #ffffff;
  }
  html, body {
    margin: 0;
    width: 1200px;
    height: 963px;
    overflow: hidden;
    background: var(--stage);
    font-family: "Poppins", sans-serif;
  }
  .stage {
    position: relative;
    width: 1200px;
    height: 963px;
    display: flex;
    align-items: center;
    justify-content: center;
    gap: 40px;
  }
  .card {
    position: relative;
    width: 540px;
    height: 309px;
    border-radius: 16px;
    overflow: hidden;
    box-shadow: 0 14px 30px rgba(0,0,0,.55);
  }
  /* Front: contact side */
  .card-front { background: var(--card-white); }
  .front-band {
    position: absolute;
    inset: 0;
    width: 100%;
    height: 100%;
  }
  .front-wordmark {
    position: absolute;
    top: 38px;
    left: 150px;
    display: flex;
    align-items: center;
    gap: 12px;
    color: var(--brand-blue);
    font-weight: 600;
    font-size: 30px;
    letter-spacing: 1px;
  }
  .mark-square {
    width: 18px;
    height: 18px;
    background: var(--brand-blue);
  }
  .contact {
    position: absolute;
    left: 34px;
    top: 122px;
    color: var(--text-white);
  }
  .contact-name {
    margin: 0;
    font-weight: 700;
    font-size: 21px;
    text-transform: uppercase;
    letter-spacing: .5px;
  }
  .contact-role {
    margin: 0 0 8px;
    font-size: 12px;
  }
  .contact-address {
    margin: 0 0 8px;
    font-size: 11.5px;
    line-height: 1.35;
  }
  .contact-line {
    display: flex;
    align-items: center;
    gap: 7px;
    margin: 0 0 3px;
    font-size: 11.5px;
  }
  .contact-line svg { width: 11px; height: 11px; flex: none; }

  /* Back: brand side */
  .card-back {
    background: linear-gradient(135deg, var(--dark-card-a), var(--dark-card-b));
    display: flex;
    align-items: center;
    justify-content: center;
  }
  .back-wordmark {
    display: flex;
    align-items: center;
    gap: 16px;
    color: var(--brand-cyan);
    font-weight: 600;
    font-size: 38px;
    letter-spacing: 1px;
  }
  .back-wordmark .mark-square {
    width: 26px;
    height: 26px;
    background: var(--brand-cyan);
  }
</style>
</head>
<body>
<main class="stage">
  <section class="card card-front" aria-label="Business card, contact side">
    <svg class="front-band" viewBox="0 0 540 309" preserveAspectRatio="none" aria-hidden="true">
      <polygon points="0,110 470,110 540,165 410,285 0,285" fill="var(--brand-blue)"/>
    </svg>
    <div class="front-wordmark"><span class="mark-square"></span>RWT Fittings Ltd</div>
    <div class="contact">
      <p class="contact-name">Marco Peltieri</p>
      <p class="contact-role">Owner &amp; Manager</p>
      <p class="contact-address">1407-5194 Linden Row<br>Burnaby BC, V5H 2K9</p>
      <p class="contact-line">
        <svg viewBox="0 0 24 24"><path fill="#fff" d="M6.6 10.8a15 15 0 0 0 6.6 6.6l2.2-2.2a1 1 0 0 1 1-.25 11.4 11.4 0 0 0 3.6.57 1 1 0 0 1 1 1V20a1 1 0 0 1-1 1A17 17 0 0 1 3 4a1 1 0 0 1 1-1h3.5a1 1 0 0 1 1 1c0 1.25.2 2.45.57 3.57a1 1 0 0 1-.25 1z"/></svg>
        16045518293
      </p>
      <p class="contact-line">
        <svg viewBox="0 0 24 24"><rect x="2" y="5" width="20" height="14" rx="1" fill="none" stroke="#fff" stroke-width="2"/><path d="M2 6l10 7 10-7" fill="none" stroke="#fff" stroke-width="2"/></svg>
        RWTFittings@mailbox-demo.com
      </p>
      <p class="contact-line">
        <svg viewBox="0 0 24 24"><circle cx="12" cy="12" r="10" fill="none" stroke="#fff" stroke-width="2"/><path d="M2 12h20M12 2c3 3 3 17 0 20M12 2c-3 3-3 17 0 20" fill="none" stroke="#fff" stroke-width="1.6"/></svg>
        www.rwtfittings-demo.com
      </p>
    </div>
  </section>

  <section class="card card-back" aria-label="Business card, brand side">
    <div class="back-wordmark"><span class="mark-square"></span>RWT Fittings Ltd</div>
  </section>
</main>
</body>
</html>
```